Business cards - BRENT Roofing & Siding

We need simple business cards made up for our Roofing & Siding business based in Calgary Alberta.
The logo on one side of the card and potentially our slogan "Solid roofs, honest work, every season".
The other side could have:
-A small logo
-Rep name:
-Rep cell phone:
-Rep email:
-Office phone: 403-684-2093
-Website: PrairieShingleWorks.com

We would like to incorporate the colours from our logo, especially the lite blue on the jpeg file. I have attached the ai file and jpeg file. We like the colours better on the jpeg file.

I do not require a money back guarantee

```html
<!DOCTYPE html>
<html lang="en">
<head>
<meta charset="utf-8">
<title>BRENT Roofing &amp; Siding – Business Cards</title>
<link href="https://fonts.googleapis.com/css2?family=Exo+2:wght@400;500;700&display=swap" rel="stylesheet">
<style>
  :root {
    --stage: #e9ebee;
    --card-white: #ffffff;
    --brand-blue: #0a8bf2;
    --deep-blue: #0a6bc0;
    --ink: #1c1c1c;
    --accent-red: #e3262e;
  }
  * { box-sizing: border-box; margin: 0; padding: 0; }
  html, body { width: 1200px; height: 718px; overflow: hidden; }
  body {
    background: var(--stage);
    font-family: "Exo 2", sans-serif;
    position: relative;
  }
  .card {
    position: absolute;
    top: 204px;
    width: 540px;
    height: 310px;
    border-radius: 18px;
    overflow: hidden;
    box-shadow: 0 8px 24px rgba(0,0,0,0.18);
  }
  .card-front { left: 40px; background: var(--card-white); }
  .card-back { left: 620px; background: var(--brand-blue); color: #fff; }

  .roof-shape { position: absolute; inset: 0; }

  .wordmark { position: absolute; display: flex; align-items: center; gap: 10px; }
  .wordmark-mark { width: 14px; height: 14px; flex: none; }
  .wordmark-name { font-weight: 700; letter-spacing: 1px; white-space: nowrap; }

  .card-front .wordmark { left: 52px; top: 70px; }
  .card-front .wordmark-mark { background: var(--brand-blue); }
  .card-front .wordmark-name { color: var(--ink); font-size: 21px; }

  .rep { position: absolute; left: 56px; top: 176px; }
  .rep-name { color: var(--brand-blue); font-weight: 700; font-size: 23px; letter-spacing: 0.3px; white-space: nowrap; }
  .rep-title { color: var(--accent-red); font-size: 16px; margin-top: -1px; }

  .contact {
    position: absolute;
    right: 22px;
    top: 140px;
    list-style: none;
    color: #fff;
    font-size: 12.5px;
    text-align: right;
    line-height: 19px;
  }
  .contact li { display: flex; justify-content: flex-end; align-items: center; gap: 7px; white-space: nowrap; }
  .contact svg { width: 11px; height: 11px; flex: none; }
  .contact .no-icon { padding-right: 18px; }

  .card-back .wordmark {
    left: 0; right: 0; top: 118px;
    justify-content: center;
  }
  .card-back .wordmark-mark { background: #fff; width: 18px; height: 18px; }
  .card-back .wordmark-name { color: #fff; font-size: 32px; }
  .slogan {
    position: absolute;
    left: 0; right: 0; bottom: 54px;
    text-align: center;
    font-size: 15px;
    letter-spacing: 0.6px;
    text-transform: uppercase;
  }
</style>
</head>
<body>

<section class="card card-front" aria-label="Business card front">
  <svg class="roof-shape" viewBox="0 0 540 310" aria-hidden="true">
    <polygon points="200,310 430,52 540,118 540,128 430,62 213,310" fill="var(--brand-blue)"/>
    <polygon points="230,310 432,76 540,140 540,310" fill="var(--deep-blue)"/>
  </svg>

  <div class="wordmark">
    <span class="wordmark-mark"></span>
    <span class="wordmark-name">BRENT Roofing &amp; Siding</span>
  </div>

  <div class="rep">
    <p class="rep-name">DALE WHITCOMB</p>
    <p class="rep-title">Managing Director</p>
  </div>

  <ul class="contact">
    <li>2742 - 9 Avenue S.E.
      <svg viewBox="0 0 12 12"><path d="M6 0.5a4 4 0 0 0-4 4c0 3 4 7 4 7s4-4 4-7a4 4 0 0 0-4-4zm0 5.6a1.6 1.6 0 1 1 0-3.2 1.6 1.6 0 0 1 0 3.2z" fill="#fff"/></svg></li>
    <li class="no-icon">Calgary, Alberta T2A 0K4</li>
    <li>403-684-2093
      <svg viewBox="0 0 12 12"><path d="M2.5 1l2 0.2 1 2.6-1.3 1a6.5 6.5 0 0 0 3 3l1-1.3 2.6 1 0.2 2A1.5 1.5 0 0 1 9.5 11 8.5 8.5 0 0 1 1 2.5 1.5 1.5 0 0 1 2.5 1z" fill="#fff"/></svg></li>
    <li>403-684-2093
      <svg viewBox="0 0 12 12"><rect x="3" y="0.5" width="6" height="11" rx="1" fill="none" stroke="#fff" stroke-width="1.2"/><circle cx="6" cy="9.6" r="0.7" fill="#fff"/></svg></li>
    <li>dale@prairieshingleworks.com
      <svg viewBox="0 0 12 12"><rect x="0.6" y="2.2" width="10.8" height="7.6" fill="none" stroke="#fff" stroke-width="1.1"/><path d="M0.8 2.6 6 6.6l5.2-4" fill="none" stroke="#fff" stroke-width="1.1"/></svg></li>
    <li>PrairieShingleWorks.com
      <svg viewBox="0 0 12 12"><circle cx="6" cy="6" r="5" fill="none" stroke="#fff" stroke-width="1.1"/><ellipse cx="6" cy="6" rx="2.2" ry="5" fill="none" stroke="#fff" stroke-width="1"/><path d="M1 6h10" stroke="#fff" stroke-width="1"/></svg></li>
  </ul>
</section>

<section class="card card-back" aria-label="Business card back">
  <div class="wordmark">
    <span class="wordmark-mark"></span>
    <span class="wordmark-name">BRENT Roofing &amp; Siding</span>
  </div>
  <p class="slogan">Solid roofs, honest work, every season</p>
</section>

</body>
</html>
```